Health Care Company with Logo Needs Business Cards designed

We are a luxury behavioral health company looking for business cards design we already have a logo and are looking for someone to design a sophisticated luxurious looking business card. Please note that Card design should be captivating just like the logo and also encompass the logo color

Industry/Entity Type

Healthcare

Contact Information for Business Card

Logo,company name, tagline, my name and title, contact details, and physical address

```html
<!DOCTYPE html>
<html lang="en">
<head>
<meta charset="utf-8">
<title>Corvane Behavioral Health – Business Card</title>
<link href="https://fonts.googleapis.com/css2?family=Roboto:wght@300;400;700&display=swap" rel="stylesheet">
<style>
  :root {
    --stage: #2a2a2c;
    --card-white: #ffffff;
    --brand-purple: #7b3b9a;
    --brand-purple-deep: #5a2475;
    --brand-purple-light: #a44fd0;
    --brand-blue: #1fa6e0;
    --ink: #1c1c1c;
    --rule: #9a9a9a;
  }
  * { margin: 0; padding: 0; box-sizing: border-box; }
  html, body {
    width: 1200px; height: 1108px; overflow: hidden;
    background: var(--stage);
    font-family: "Roboto", Arial, sans-serif;
  }
  .stage {
    position: relative; width: 1200px; height: 1108px;
    display: flex; justify-content: center; align-items: center; gap: 60px;
  }
  .card {
    width: 360px; height: 630px; border-radius: 22px;
    position: relative; overflow: hidden;
    box-shadow: 0 14px 30px rgba(0,0,0,.45);
  }
  .card-front {
    background: var(--card-white);
    display: flex; flex-direction: column; align-items: center;
    text-align: center; padding: 120px 20px 0;
  }
  .brand-lockup { display: flex; flex-direction: column; align-items: center; }
  .brand-mark {
    width: 18px; height: 18px; background: var(--brand-purple);
    margin-bottom: 14px;
  }
  .brand-name {
    color: var(--brand-purple); font-weight: 700; font-size: 28px;
    letter-spacing: -0.3px; line-height: 1.1; white-space: nowrap;
  }
  .brand-tagline {
    color: var(--brand-blue); font-size: 10px; font-weight: 400;
    letter-spacing: 1.9px; text-transform: uppercase; margin-top: 8px;
    white-space: nowrap;
  }
  .person { margin-top: 86px; }
  .person-name {
    color: var(--brand-purple); font-weight: 300; font-size: 30px; line-height: 1.1;
  }
  .person-title { color: var(--ink); font-size: 17px; font-weight: 400; margin-top: 2px; }
  .icon-rule {
    display: flex; align-items: center; gap: 8px; width: 260px; margin-top: 20px;
  }
  .icon-rule .line { flex: 1; height: 1px; background: var(--rule); }
  .contact-icon {
    width: 26px; height: 26px; border-radius: 5px; background: var(--brand-purple);
    display: flex; align-items: center; justify-content: center;
  }
  .contact-list { list-style: none; margin-top: 12px; color: var(--ink); font-size: 17px; line-height: 1.45; }
  .divider { width: 260px; height: 1px; background: var(--rule); margin-top: 18px; }
  .address { color: var(--ink); font-size: 17px; line-height: 1.35; margin-top: 14px; font-style: normal; }

  .card-back {
    background: linear-gradient(160deg, var(--brand-purple-light) 0%, var(--brand-purple) 45%, var(--brand-purple-deep) 100%);
  }
  .back-pattern { position: absolute; inset: 0; }
  .back-brand {
    position: absolute; right: 62px; bottom: 150px;
    color: var(--card-white); font-weight: 700; font-size: 26px;
  }
</style>
</head>
<body>
<main class="stage">
  <section class="card card-front" aria-label="Business card front">
    <div class="brand-lockup">
      <span class="brand-mark"></span>
      <h1 class="brand-name">Corvane Behavioral Health</h1>
      <p class="brand-tagline">Committed to calm, care and renewal</p>
    </div>

    <div class="person">
      <h2 class="person-name">Daniel Marsh</h2>
      <p class="person-title">Managing Director</p>
    </div>

    <div class="icon-rule">
      <span class="line"></span>
      <span class="contact-icon" aria-label="Phone">
        <svg width="16" height="16" viewBox="0 0 16 16"><path d="M4 2 L6 5 L5 6.5 C6 8.5 7.5 10 9.5 11 L11 10 L14 12 L12.5 14 C7 13.5 2.5 9 2 3.5 Z" fill="#fff"/></svg>
      </span>
      <span class="contact-icon" aria-label="Email">
        <svg width="16" height="16" viewBox="0 0 16 16"><rect x="1.5" y="3.5" width="13" height="9" fill="none" stroke="#fff" stroke-width="1.4"/><path d="M1.5 3.5 L8 9 L14.5 3.5" fill="none" stroke="#fff" stroke-width="1.4"/></svg>
      </span>
      <span class="contact-icon" aria-label="Website">
        <svg width="16" height="16" viewBox="0 0 16 16"><circle cx="8" cy="8" r="6" fill="none" stroke="#fff" stroke-width="1.4"/><path d="M2 8 H14 M8 2 C5 5 5 11 8 14 M8 2 C11 5 11 11 8 14" fill="none" stroke="#fff" stroke-width="1.1"/></svg>
      </span>
      <span class="line"></span>
    </div>

    <ul class="contact-list">
      <li>044-987 654 321</li>
      <li>info@corvanebh.com</li>
      <li>www.corvanebh.com</li>
    </ul>

    <div class="divider"></div>

    <address class="address">87 Maple Court, Suite 4<br>30218, Country Name</address>
  </section>

  <section class="card card-back" aria-label="Business card back">
    <div class="back-pattern" role="img" aria-label="Repeating embossed brand monogram pattern in purple tones"></div>
    <p class="back-brand">Corvane</p>
  </section>
</main>
</body>
</html>
```